CPA Graduation Party

I need to make simple invitation for my sister's recent success, passing the CPA (Certified Public Accountant) exam. It is a surprise party. I want very simple and professional looking invitation. My only requirements are that you don't use any graduation caps or gowns due to the fact that it's not an actual graduation. It's a series of exams that she passes. Be creative with the design but once again, keep it professional. I have attached a font called iScriptSTD. I liked the font so was thinking about using it. But it's not necessary. If you have something slimier or better, please use it.

I was planning on printing on a specific kind of paper. It's called pearlized ivory cardstock. It has a little coating and shine on it and since it's ivory, I was thinking about the main color of the invitation to be burgundy type. For example, see the following RGB: R204, G0, B102.

Party info:
Name: Revathi
Date & Time: Saturday, March 8th, 2014 at 6:00pm
Location: Kesar Mahal. 413 Weaverly Lane Parsippany, NJ 07089

I know I didn't provide a lot of info for the invite but please be creative.  Use general knowledge and other formal party invites as examples. I am not looking for a name, date and location as three bullets on the card.

Also, I forgot to mention the size of the invite.  It should be 5.5x8.5.  Thank you.

• graduation caps and/or gowns

```html
<!DOCTYPE html>
<html lang="en">
<head>
<meta charset="utf-8">
<title>Revathi's Celebration Party Invitation</title>
<link rel="stylesheet" href="https://fonts.googleapis.com/css2?family=Kaushan+Script&family=Tinos&display=swap">
<style>
  :root {
    --berry: #cc0066;
    --berry-tint: #eab3cf;
    --paper: #ffffff;
    --pearl: #f0f0f0;
    --ink-light: #ffffff;
    --rule: rgba(255, 255, 255, 0.75);
  }
  html, body {
    margin: 0;
    padding: 0;
    width: 1200px;
    height: 1000px;
    overflow: hidden;
    background: var(--paper);
  }
  .invitation {
    position: absolute;
    left: 305px;
    top: 48px;
    width: 578px;
    height: 894px;
  }
  .ornament-band {
    position: absolute;
    left: 0;
    width: 578px;
    height: 194px;
    background: linear-gradient(90deg, var(--berry-tint) 0%, var(--pearl) 30%, var(--pearl) 70%, var(--berry-tint) 100%);
  }
  .ornament-band--top { top: 0; }
  .ornament-band--bottom { top: 700px; }
  .message-panel {
    position: absolute;
    left: 0;
    top: 194px;
    width: 578px;
    height: 506px;
    background: var(--berry);
    color: var(--ink-light);
    font-family: "Tinos", "Times New Roman", serif;
    text-align: center;
  }
  .eyebrow, .subtitle, .venue-heading {
    position: absolute;
    left: 0;
    width: 100%;
    margin: 0;
    font-size: 17px;
    font-weight: 400;
    line-height: 20px;
    letter-spacing: 0.2px;
  }
  .eyebrow { top: 82px; }
  .honoree {
    position: absolute;
    left: 0;
    width: 100%;
    top: 104px;
    margin: 0;
    font-family: "Kaushan Script", cursive;
    font-size: 82px;
    font-weight: 400;
    line-height: 100px;
  }
  .subtitle { top: 216px; }
  .divider {
    position: absolute;
    left: 98px;
    top: 266px;
    width: 386px;
    height: 20px;
  }
  .venue-heading { top: 306px; }
  .venue-details {
    position: absolute;
    left: 0;
    width: 100%;
    top: 354px;
    margin: 0;
    font-size: 17px;
    line-height: 26px;
  }
</style>
</head>
<body>
  <main class="invitation">
    <div class="ornament-band ornament-band--top" role="img" aria-label="Decorative swirling filigree pattern in berry on pearl white"></div>

    <section class="message-panel">
      <p class="eyebrow">YOU ARE INVITED TO</p>
      <h1 class="honoree">Revathi’s</h1>
      <p class="subtitle">CELEBRATION PARTY</p>

      <svg class="divider" viewBox="0 0 386 20" aria-hidden="true">
        <line x1="0" y1="10" x2="184" y2="10" stroke="rgba(255,255,255,0.75)" stroke-width="1"/>
        <line x1="202" y1="10" x2="386" y2="10" stroke="rgba(255,255,255,0.75)" stroke-width="1"/>
        <polygon points="193,1 199,10 193,19 187,10" fill="#ffffff"/>
      </svg>

      <h2 class="venue-heading">THE PARTY WILL BE HELD AT</h2>
      <p class="venue-details">
        Kesar Mahal. 413 Weaverly Lane Parsippany, NJ 07089<br>
        on Saturday, March 8th, 2014 at 6.00pm
      </p>
    </section>

    <div class="ornament-band ornament-band--bottom" role="img" aria-label="Decorative swirling filigree pattern in berry on pearl white"></div>
  </main>
</body>
</html>
```